Coffee Bag Design for Tollbury Coffee

We’re excited to invite you to help us bring Tollbury Coffee to life on grocery store shelves with a design that embodies our mission of spreading goodness and creating a lasting impact. Tollbury Coffee represents warmth, positivity, and the power of small actions to create ripples of goodness. Each cup not only offers a rich, gourmet coffee experience but also gives back to the community, with $2 from each bag supporting local food banks.

To reflect this vision, we’d love for the design to feature a dark (greyish) blue as the base color to convey depth and quality, complemented by a vibrant light blue that will catch the eye and add energy. Tan or gold accents could add an elegant touch and a feeling of warmth. We are aiming for a look that feels uplifting and engaging, with simplicity and elegance, yet stands out amid other brands on the shelf.

I am attaching the dimension of the bag.

Other information that needs to be listed:
Ingredients: 100% Arabica Coffee
Net Wt. 12 oz. (340 g)
Roasted and distributed by:
Name
Address
email

Text on the back of the bag:
Tollbury Coffee is crafted with a belief that kindness and positivity can spread, touching countless lives with every sip. This gourmet blend delivers a rich taste experience while giving back, as $2 from each bag sold is donated to local food banks to help those in need. Enjoy the warmth and goodness in each cup, knowing you’re making a difference with every purchase.

Thank you!

```html
<!DOCTYPE html>
<html lang="en">
<head>
<meta charset="utf-8">
<title>Tollbury Coffee – Bag Front</title>
<link href="https://fonts.googleapis.com/css2?family=Montserrat:ital,wght@0,600;0,700;1,700&display=swap" rel="stylesheet">
<style>
  :root {
    --backdrop: #3a5468;
    --navy: #27394a;
    --navy-deep: #1c2b38;
    --sky: #5bc6f0;
    --band: #56b2d8;
    --panel: #b7d7e6;
    --tan: #a9a57b;
    --gold: #c6a65c;
    --frame: #d8b88e;
    --white: #ffffff;
  }
  * { margin: 0; padding: 0; box-sizing: border-box; }
  html, body { width: 1200px; height: 1200px; overflow: hidden; }
  body { background: var(--backdrop); font-family: "Montserrat", sans-serif; position: relative; }

  .bag-front {
    position: absolute; left: 223px; top: 125px; width: 778px; height: 934px;
    background: var(--navy); overflow: hidden;
  }
  .sunburst-art {
    position: absolute; left: 0; top: 0; width: 778px; height: 435px;
    background: radial-gradient(ellipse at 50% 100%, #6fa6b8 0%, #4f92ad 30%, #8f9474 60%, var(--navy-deep) 100%);
  }
  .sunburst-fade {
    position: absolute; left: 0; top: 380px; width: 778px; height: 80px;
    background: linear-gradient(to bottom, rgba(39,57,74,0), var(--navy));
  }
  .cup-art {
    position: absolute; left: 299px; top: 130px; width: 304px; height: 350px;
    border-radius: 40% 40% 50% 50%;
    background: linear-gradient(to bottom, #e8ecef 0%, #5bc6f0 55%, #d3b38b 100%);
  }
  .brand-name {
    position: absolute; left: 0; width: 778px; top: 488px;
    text-align: center; color: var(--sky);
    font-weight: 700; font-size: 84px; line-height: 86px; letter-spacing: 1px;
  }
  .info-band {
    position: absolute; left: 0; top: 680px; width: 778px; height: 254px; background: var(--band);
  }
  .info-stripe {
    position: absolute; left: 0; top: 861px; width: 778px; height: 19px; background: var(--navy);
  }
  .info-panel {
    position: absolute; left: 218px; top: 701px; width: 341px; height: 188px;
    background: var(--panel); box-shadow: 0 4px 10px rgba(20,60,90,0.35);
  }
  .arabica-seal {
    position: absolute; left: 43px; top: 778px; width: 122px; height: 122px; border-radius: 50%;
    background: radial-gradient(circle at 45% 40%, #fff6c4 0%, #ead79a 50%, #a88b52 100%);
    box-shadow: 6px 6px 0 rgba(60,130,170,0.6);
    display: flex; flex-direction: column; align-items: center; justify-content: center;
    color: var(--navy); font-style: italic; font-weight: 700; text-align: center;
  }
  .arabica-seal .pct { font-size: 25px; line-height: 26px; }
  .arabica-seal .label { font-size: 14px; line-height: 18px; }
  .net-weight {
    position: absolute; left: 635px; top: 803px; width: 94px; height: 77px;
    background: var(--navy); border-radius: 18px 18px 0 0;
    color: var(--white); font-weight: 600; font-size: 13px; line-height: 18px;
    letter-spacing: 1px; text-align: center; padding-top: 12px;
  }
  .frame-line { position: absolute; left: 0; top: 0; pointer-events: none; }
</style>
</head>
<body>
  <main class="bag-front">
    <div class="sunburst-art" role="img" aria-label="Sunburst rays in light blue, tan and dark navy radiating from the cup"></div>
    <div class="sunburst-fade"></div>
    <div class="cup-art" role="img" aria-label="Illustration of a hand holding a steaming light blue coffee cup"></div>

    <h1 class="brand-name">TOLLBURY<br>COFFEE</h1>

    <div class="info-band"></div>
    <div class="info-stripe"></div>
    <div class="info-panel"></div>

    <div class="arabica-seal">
      <span class="pct">100%</span>
      <span class="label">ARABICA</span>
      <span class="label">COFFEE</span>
    </div>

    <div class="net-weight">NET WT<br>12 OZ.<br>(340 G)</div>

    <svg class="frame-line" width="778" height="934" viewBox="0 0 778 934">
      <rect x="24.5" y="28.5" width="730" height="878" rx="26" fill="none" stroke="var(--frame)" stroke-width="1.2"/>
    </svg>
  </main>
</body>
</html>
```